Brookvane Consulting Business Card Design

Business Card Design for Brookvane Consulting. Brookvane Consulting is a boutique consultancy based in Atlanta, GA., that specializes in marketing strategy, organization planning, and leadership development. We provide solutions for small businesses and startups as well as Vantage 300 companies.

http://brookvaneconsulting.com/

Target Market(s)

We provide solutions for small businesses and startups as well as Vantage 300 companies.

Industry/Entity Type

Consulting

Contact Information for Business Card

Two sided business card with priority on contact information, logo, tag line (Clarity to Plan Better, Act Sooner, Grow Further)

Colors

Designer to choose colors to be used in the design.

Requirements
Must have
• contact information, logo, tag line (Clarity to Plan Better, Act Sooner, Grow Further)
• Simple no over communication.
Nice to have
• I would like to see different placements of logo and creative use of both sides of the card
Should not have
• Do not put too much information on the card.

```html
<!DOCTYPE html>
<html lang="en">
<head>
<meta charset="utf-8">
<title>Brookvane Consulting Business Card</title>
<link rel="stylesheet" href="https://fonts.googleapis.com/css2?family=Montserrat:wght@400;600&family=Pacifico&display=swap">
<style>
  :root {
    --backdrop: #4a4a4a;
    --card: #333333;
    --ink: #ffffff;
    --ink-soft: #e6e6e6;
  }
  * { margin: 0; padding: 0; box-sizing: border-box; }
  html, body {
    width: 799px;
    height: 1200px;
    overflow: hidden;
    background: var(--backdrop);
  }
  .sheet {
    position: relative;
    width: 799px;
    height: 1200px;
  }
  .card {
    position: absolute;
    left: 90px;
    width: 620px;
    height: 354px;
    background: var(--card);
    border-radius: 22px;
    box-shadow: 0 10px 24px rgba(0, 0, 0, 0.35);
    color: var(--ink);
  }
  .card--front { top: 130px; }
  .card--back { top: 716px; }

  .brand {
    display: flex;
    align-items: center;
    gap: 12px;
    font-family: "Montserrat", Arial, sans-serif;
    font-weight: 600;
    letter-spacing: 0.04em;
    color: var(--ink);
    white-space: nowrap;
  }
  .brand__mark {
    flex: none;
    border-radius: 50%;
    background: var(--ink);
  }
  .card--front .brand {
    position: absolute;
    left: 0;
    right: 0;
    top: 140px;
    justify-content: center;
    font-size: 34px;
  }
  .card--front .brand__mark { width: 22px; height: 22px; }

  .back-logo {
    position: absolute;
    right: 40px;
    top: 56px;
    text-align: right;
  }
  .card--back .brand {
    justify-content: flex-end;
    font-size: 25px;
  }
  .card--back .brand__mark { width: 16px; height: 16px; }
  .tagline {
    margin-top: 8px;
    font-family: "Montserrat", Arial, sans-serif;
    font-size: 11.5px;
    font-weight: 400;
    letter-spacing: 0.03em;
    color: var(--ink-soft);
    white-space: nowrap;
  }

  .contact {
    position: absolute;
    left: 42px;
    top: 140px;
    font-family: Arial, Helvetica, sans-serif;
    font-style: normal;
    font-size: 14px;
    line-height: 1.45;
    color: var(--ink);
  }
  .contact__name {
    font-family: "Pacifico", cursive;
    font-size: 19px;
    line-height: 1.2;
    margin-bottom: 10px;
  }
  .contact__line { display: block; }
</style>
</head>
<body>
  <main class="sheet">
    <section class="card card--front" aria-label="Card front">
      <div class="brand">
        <span class="brand__mark" aria-hidden="true"></span>
        <span class="brand__name">Brookvane Consulting</span>
      </div>
    </section>

    <section class="card card--back" aria-label="Card back">
      <div class="back-logo">
        <div class="brand">
          <span class="brand__mark" aria-hidden="true"></span>
          <span class="brand__name">Brookvane Consulting</span>
        </div>
        <p class="tagline">Clarity to Plan Better, Act Sooner, Grow Further</p>
      </div>

      <address class="contact">
        <p class="contact__name">Dorian</p>
        <span class="contact__line">555-010-4827</span>
        <span class="contact__line">dorian@brookvaneconsulting.com</span>
        <span class="contact__line">www.brookvaneconsulting.com</span>
      </address>
    </section>
  </main>
</body>
</html>
```